Business Card Design (NEW FILES)

ATTENTION: New vector files are available. Please update your design to reflect/use the new (better resolution) logo images.

Seeking a unique and professional business card design for a commercial drone photography/videography business. The layout should feature
the logo (attached) and include the following information:
Owen Tarrick
614-502-7738
www.skylarkreelworks.example
NRD Certified Remote Pilot

Owen Tarrick

```html
<!DOCTYPE html>
<html lang="en">
<head>
<meta charset="utf-8">
<title>Skylark Reelworks – Business Card</title>
<link rel="stylesheet" href="https://fonts.googleapis.com/css2?family=Open+Sans:wght@400;600;700&display=swap">
<style>
  :root {
    --page-bg: #222222;
    --card-navy: #1a1a4b;
    --accent-orange: #e8833f;
    --text-white: #ffffff;
  }
  * { margin: 0; padding: 0; box-sizing: border-box; }
  html, body {
    width: 1200px;
    height: 780px;
    overflow: hidden;
    background: var(--page-bg);
    font-family: "Open Sans", sans-serif;
  }
  .canvas {
    width: 1200px;
    height: 780px;
    display: flex;
    align-items: center;
    justify-content: center;
    gap: 40px;
  }
  .card {
    position: relative;
    width: 540px;
    height: 309px;
    background: var(--card-navy);
    border-radius: 22px;
    overflow: hidden;
    color: var(--text-white);
  }
  .accent-band {
    position: absolute;
    height: 9px;
    background: var(--accent-orange);
  }
  .accent-band--top { top: 0; left: 26px; width: 190px; }
  .accent-band--bottom { bottom: 0; right: 26px; width: 190px; }

  .brand {
    position: absolute;
    display: flex;
    align-items: center;
    gap: 10px;
    color: var(--text-white);
    font-weight: 600;
    white-space: nowrap;
  }
  .brand__dot {
    border-radius: 50%;
    background: var(--accent-orange);
    flex: none;
  }
  .card--front .brand { left: 48px; top: 78px; font-size: 22px; }
  .card--front .brand__dot { width: 14px; height: 14px; }

  .credentials {
    position: absolute;
    left: 30px;
    top: 190px;
    width: 230px;
    text-align: center;
    font-size: 14px;
    line-height: 1.55;
  }
  .divider {
    position: absolute;
    left: 0; top: 0;
    width: 540px; height: 309px;
  }
  .contact {
    position: absolute;
    left: 300px;
    top: 96px;
  }
  .contact__name {
    font-size: 27px;
    font-weight: 700;
    line-height: 1.1;
    white-space: nowrap;
  }
  .contact__first { color: var(--accent-orange); }
  .contact__role {
    font-size: 14px;
    margin-top: 2px;
    margin-bottom: 16px;
  }
  .contact__line {
    display: flex;
    align-items: center;
    gap: 8px;
    font-size: 13.5px;
    line-height: 1.9;
    white-space: nowrap;
  }
  .contact__icon { width: 13px; height: 13px; flex: none; }

  .card--back .brand {
    left: 50%;
    top: 50%;
    transform: translate(-50%, -50%);
    font-size: 36px;
    gap: 14px;
  }
  .card--back .brand__dot { width: 22px; height: 22px; }
</style>
</head>
<body>
<main class="canvas">
  <section class="card card--front" aria-label="Business card front">
    <div class="accent-band accent-band--top"></div>
    <div class="accent-band accent-band--bottom"></div>

    <div class="brand"><span class="brand__dot"></span>Skylark Reelworks</div>

    <p class="credentials">NRD Certified Remote Pilot<br>Fully Insured</p>

    <svg class="divider" viewBox="0 0 540 309" aria-hidden="true">
      <line x1="288" y1="66" x2="262" y2="238" stroke="#e8833f" stroke-width="1.2"/>
    </svg>

    <div class="contact">
      <h1 class="contact__name"><span class="contact__first">Owen</span> Tarrick</h1>
      <p class="contact__role">Owner</p>
      <p class="contact__line">
        <svg class="contact__icon" viewBox="0 0 24 24" aria-hidden="true">
          <path fill="#e8833f" d="M6.6 10.8a15.1 15.1 0 0 0 6.6 6.6l2.2-2.2a1 1 0 0 1 1-.25 11.4 11.4 0 0 0 3.6.57 1 1 0 0 1 1 1V20a1 1 0 0 1-1 1A17 17 0 0 1 3 4a1 1 0 0 1 1-1h3.5a1 1 0 0 1 1 1c0 1.25.2 2.45.57 3.57a1 1 0 0 1-.25 1z"/>
        </svg>
        614-502-7738
      </p>
      <p class="contact__line">
        <svg class="contact__icon" viewBox="0 0 24 24" aria-hidden="true">
          <circle cx="12" cy="12" r="10" fill="none" stroke="#e8833f" stroke-width="2"/>
          <ellipse cx="12" cy="12" rx="4.5" ry="10" fill="none" stroke="#e8833f" stroke-width="2"/>
          <line x1="2" y1="12" x2="22" y2="12" stroke="#e8833f" stroke-width="2"/>
        </svg>
        www.skylarkreelworks.example
      </p>
    </div>
  </section>

  <section class="card card--back" aria-label="Business card back">
    <div class="brand"><span class="brand__dot"></span>Skylark Reelworks</div>
  </section>
</main>
</body>
</html>
```